Website with a rustic Patriotic Feel

I am looking to design the
Home page I have a mock-up that has the essentials on it like our video, a small slideshow, our plans, and a coverage map, and a small sign up box to be sent a free SIM card.

Eligibility Page: Cool Background with a fill in box that lets the user know if their number is GSM or unlocked.

View Plans page: will have our plans hopefully in their colors with a cool background a walkthrough on Activation.

Activation: If you order your plan first then we send the SIM Card Basically another fill out sheet first name last name ICCID IMEI phone number email

, Contact Us: This is our Customer support page.

Steady Beacon ( this will be our About us page and will have a calendar of Community Volunteer Opportunities.. Right now I have a hodgepodge of different themes that I am going with for the web design. I would like it cohesive with the theme so all of it can fit together nicely.

At the Site map at the bottom we are looking for the basic Menu redirects. quick links to our T&Cs Customer Support and Follow US Buttons as well as a sign up for our Newsletter fill in.

Feel free to redo any of the ads. We are an MVNO like (Northpine Wireless) we provide network Voice and Data Plans our target audience is first Responders and Military. If you are wondering what that green map is its a coverage map to see where to best have coverage. Right now I have a website that uses CMS and HTML. If you are interested in doing a full redesign of our website we would love it.

Right now our website is www.tallow-linkwave.example if you need any additional information.

Target Market(s)

First Responders and Military

Coding

Coded - Design and coding required

Number of Pages Required

5+ page

Font styles to use
Sans Serif

Colors
0455a3
0493ce
f0474d
ffffff

Requirements
Must have
• Cohesive and have a powerpoint and coverage map
Should not have
• Anything flowery or kiddish

```html
<!DOCTYPE html>
<html lang="en">
<head>
<meta charset="utf-8">
<title>Keystone Signal Mobile — Home</title>
<link href="https://fonts.googleapis.com/css2?family=Roboto:wght@400;500;700;900&family=Archivo+Black&display=swap" rel="stylesheet">
<style>
:root{
  --navy:#0b3a93;
  --blue:#0455a3;
  --sky:#0493ce;
  --red:#f0474d;
  --white:#ffffff;
  --ink:#1d2433;
  --muted:#6b6658;
  --parch-1:#e9dcae;
  --parch-2:#d3bf86;
  --offer-bg:#1b2f8c;
  --offer-text:#8f93a8;
  --footer:#1c1c1e;
  --bronze-1:#d4b88c;--bronze-2:#a88a60;
  --silver-1:#ffffff;--silver-2:#bfc1c6;
  --gold-1:#ebb62a;--gold-2:#e0a12a;
  --plat-1:#6e6662;--plat-2:#2c2826;
  --dia-1:#2d8fd3;--dia-2:#1a5d9e;
}
*{margin:0;padding:0;box-sizing:border-box}
html,body{width:1200px;height:3393px;overflow:hidden}
body{position:relative;font-family:"Roboto",sans-serif;color:var(--ink);
  background:radial-gradient(ellipse at 30% 20%,var(--parch-1),var(--parch-2) 70%),var(--parch-2)}
.abs{position:absolute}
/* header */
.site-header{left:0;top:0;width:1200px;height:108px}
.brand{left:110px;top:30px;font-weight:900;font-size:26px;color:var(--blue);letter-spacing:1px}
.brand-mark{display:inline-block;width:22px;height:22px;border-radius:50%;background:var(--red);vertical-align:-3px;margin-right:8px}
.main-nav{left:375px;top:38px;display:flex;gap:34px;font-size:16px;font-weight:500}
.main-nav a{color:var(--ink);text-decoration:none;position:relative}
.main-nav a.active::after{content:"";position:absolute;left:0;right:0;bottom:-7px;height:2px;background:var(--red)}
/* hero */
.hero{left:0;top:108px;width:1200px;height:472px;
  background:linear-gradient(180deg,#7fa2c6 0%,#5d7fa6 55%,#3b5577 100%)}
.hero-title{left:55px;top:290px;font-weight:900;font-size:56px;color:var(--sky);letter-spacing:2px}
.dots{left:580px;top:552px;display:flex;gap:6px}
.dots span{width:10px;height:10px;border-radius:50%;background:var(--white)}
.dots span.on{background:var(--red)}
/* section titles */
.sec-title{left:0;width:1200px;text-align:center;font-weight:700;font-size:33px;color:var(--navy)}
.sec-title::after{content:"";display:block;width:78px;height:4px;background:var(--red);margin:14px auto 0}
.mission-text{left:158px;top:756px;width:884px;font-size:14.5px;line-height:26px;text-align:justify;text-align-last:center;color:var(--muted)}
.video{left:220px;top:1018px;width:760px;height:396px;background:radial-gradient(circle at 65% 65%,#2c5a6a,#101418 60%)}
.play{left:571px;top:1196px;width:58px;height:58px;border-radius:50%;background:var(--white)}
/* offer */
.offer{left:0;top:1509px;width:1200px;height:366px;background:linear-gradient(100deg,#19328f,var(--offer-bg) 60%,#22348a)}
.offer-flags{left:900px;top:1509px;width:300px;height:366px;background:linear-gradient(160deg,#b8364a 0%,#e6e6ee 40%,#2a3f96 75%)}
.offer-copy{left:0;top:1612px;width:1180px;text-align:center;font-family:"Archivo Black",sans-serif;color:var(--offer-text);line-height:1}
.offer-copy .l1{font-size:44px}
.offer-copy .l2{font-size:28px;margin-top:8px}
.offer-copy .l3{font-size:44px}
.offer-copy .l4{font-size:28px;margin-top:4px}
/* pricing */
.plan{top:2059px;width:211px;height:349px;border-radius:12px;color:var(--white)}
.plan h3{text-align:center;font-size:16px;font-weight:500;margin-top:18px}
.price{position:absolute;left:16px;top:54px;width:143px;height:64px;background:var(--white);border-radius:6px;
  box-shadow:6px 6px 10px rgba(0,0,0,.25);color:var(--navy);text-align:center;padding-top:12px}
.price b{display:block;font-size:16px;font-weight:700}
.price small{font-size:11px;font-weight:700}
.plan ul{position:absolute;left:48px;top:148px;list-style:none;font-size:13.5px;line-height:26px}
.plan li::before{content:"";display:inline-block;width:5px;height:5px;border-radius:50%;background:currentColor;margin-right:9px;vertical-align:2px}
.plan .sub{position:absolute;left:37px;top:286px;width:133px;height:45px;border:1px solid currentColor;
  font-weight:700;font-size:16px;line-height:43px;text-align:center}
.bronze{left:16px;background:linear-gradient(180deg,var(--bronze-1),var(--bronze-2))}
.silver{left:256px;background:linear-gradient(180deg,var(--silver-1),var(--silver-2));color:var(--navy)}
.silver ul{color:var(--ink)}
.gold{left:494px;background:linear-gradient(180deg,var(--gold-1),var(--gold-2))}
.platinum{left:734px;background:linear-gradient(180deg,var(--plat-1),var(--plat-2))}
.diamond{left:973px;background:linear-gradient(180deg,var(--dia-1),var(--dia-2))}
/* newsletter */
.news{left:0;top:2501px;width:1200px;height:531px;background:var(--navy)}
.coverage-map{left:25px;top:2565px;width:607px;height:375px;background:linear-gradient(135deg,#f4f6fa,#dfe5ef);border-radius:40% 30% 35% 25%}
.map-label{left:326px;top:2737px;background:var(--white);padding:12px 14px;font-size:16px;font-weight:500;box-shadow:0 2px 6px rgba(0,0,0,.2)}
.pin{left:278px;top:2712px}
.news-title{left:779px;top:2604px;font-size:33px;font-weight:700;color:var(--white)}
.news-title::after{content:"";display:block;width:76px;height:4px;background:var(--red);margin:12px 0 0 75px}
.field{left:779px;width:294px;height:52px;background:var(--white);font-size:14px;color:#666;padding:18px 18px}
.news-btn{left:779px;top:2871px;width:157px;height:51px;background:var(--red);color:var(--white);font-weight:700;font-size:16px;text-align:center;line-height:51px}
/* footer */
.site-footer{left:0;top:3032px;width:1200px;height:361px;background:var(--footer);color:var(--white)}
.f-col{top:3085px}
.f-col h4{font-size:16px;font-weight:700;margin-bottom:22px}
.f-col a{display:block;color:var(--white);text-decoration:none;font-size:14.5px;line-height:26px}
.social a{display:flex;align-items:center;gap:12px;line-height:38px;font-size:16px}
.social i{width:30px;height:30px;border-radius:50%;background:#2a2f3a;display:inline-block}
.rule{left:101px;top:3306px;width:1013px;height:1px;background:#666}
.copy{left:0;top:3336px;width:1200px;text-align:center;font-size:11px;color:#ddd}
</style>
</head>
<body>

<header class="site-header abs">
  <div class="brand abs"><span class="brand-mark"></span>Keystone Signal</div>
  <nav class="main-nav abs">
    <a class="active" href="#">Home</a><a href="#">View Plans</a><a href="#">Activate Today</a><a href="#">Contact Us</a><a href="#">Steady Beacon</a><a href="#">My Account</a>
  </nav>
</header>

<section class="hero abs" role="img" aria-label="Slideshow banner: first responders and service members in front of a naval ship and rescue helicopter at sea"></section>
<div class="hero-title abs">Keystone Signal Mobile</div>
<div class="dots abs"><span></span><span class="on"></span><span></span></div>

<h2 class="sec-title abs" style="top:666px">OUR MISSION</h2>
<p class="mission-text abs">Lorem ipsum dolor sit amet, consectetur adipiscing elit, sed do eiusmod tempor incididunt ut labore et dolore magna aliqua. Ut enim ad minim veniam, quis nostrud exercitation ullamco laboris nisi ut aliquip ex ea commodo consequat. Duis aute irure dolor in reprehenderit in voluptate velit esse cillum dolore eu fugiat nulla pariatur. Excepteur sint occaecat cupidatat non proident</p>

<h2 class="sec-title abs" style="top:914px">OUR VIDEOS</h2>
<div class="video abs" role="img" aria-label="Video thumbnail: illustrated globe with cell towers and network partner bubbles"></div>
<div class="play abs"><svg width="58" height="58" viewBox="0 0 58 58"><path d="M24 19 L40 29 L24 39 Z" fill="#0b3a93"/></svg></div>

<section class="offer abs"></section>
<div class="offer-flags abs" role="img" aria-label="American flags waving"></div>
<div class="offer-copy abs">
  <div class="l1">LIMITED-TIME OFFER!</div>
  <div class="l2">Military and first responders will recieve their first</div>
  <div class="l3">2 DECEMBERS FOR FREE</div>
  <div class="l4">with a two year contract.</div>
</div>

<h2 class="sec-title abs" style="top:1960px">OUR PRICING PLAN</h2>

<div class="plan bronze abs"><h3>BRONZE</h3><div class="price"><b>$20.00 /</b><small>MONTH</small></div>
<ul><li>Data &amp; Voice</li><li>Unlimited Talk</li><li>Unlimited Text</li><li>100MB</li><li>4G LTE DATA</li></ul><div class="sub">SUBSCRIBE</div></div>
<div class="plan silver abs"><h3>SILVER</h3><div class="price"><b>$25.00 /</b><small>MONTH</small></div>
<ul><li>Data &amp; Voice</li><li>Unlimited Talk</li><li>Unlimited Text</li><li>1GB</li><li>4G LTE DATA</li></ul><div class="sub">SUBSCRIBE</div></div>
<div class="plan gold abs"><h3>GOLD</h3><div class="price"><b>$20.00 /</b><small>MONTH</small></div>
<ul><li>Data &amp; Voice</li><li>Unlimited Talk</li><li>Unlimited Text</li><li>3GB</li><li>4G LTE DATA</li></ul><div class="sub">SUBSCRIBE</div></div>
<div class="plan platinum abs"><h3>PLATINUM</h3><div class="price"><b>$20.00 /</b><small>MONTH</small></div>
<ul><li>Data &amp; Voice</li><li>Unlimited Talk</li><li>Unlimited Text</li><li>5GB</li><li>4G LTE DATA</li></ul><div class="sub">SUBSCRIBE</div></div>
<div class="plan diamond abs"><h3>DIAMOND</h3><div class="price"><b>$20.00 /</b><small>MONTH</small></div>
<ul><li>Data &amp; Voice</li><li>Unlimited Talk</li><li>Unlimited Text</li><li>Unlimited Data</li><li>Upto 22 GB</li></ul><div class="sub">SUBSCRIBE</div></div>

<section class="news abs"></section>
<div class="coverage-map abs" role="img" aria-label="Coverage map of the United States with state outlines"></div>
<svg class="pin abs" width="22" height="30" viewBox="0 0 22 30"><path d="M11 1C5.5 1 1 5.3 1 10.8 1 18 11 29 11 29S21 18 21 10.8C21 5.3 16.5 1 11 1Z" fill="#f0474d"/><circle cx="11" cy="11" r="4" fill="#fff"/></svg>
<div class="map-label abs">Keystone Signal</div>
<h2 class="news-title abs">KEYSTONE NEWSLETTER</h2>
<div class="field abs" style="top:2708px">Name</div>
<div class="field abs" style="top:2790px">Email</div>
<div class="news-btn abs">SUBSCRIBE</div>

<footer class="site-footer abs"></footer>
<div class="f-col abs" style="left:153px"><h4>MAIN MENU</h4><a href="#">Home</a><a href="#">Catalog</a><a href="#">View Plans</a><a href="#">Activate Today</a><a href="#">Contact Us</a><a href="#">Steady Beacon</a></div>
<div class="f-col abs" style="left:374px"><h4>QUICK LINKS</h4><a href="#">Terms &amp; Conditions</a><a href="#">Activating Your Service</a><a href="#">Acceptable Use Policy</a><a href="#">Wireless Privacy Policy</a><a href="#">Coverage Map</a></div>
<div class="f-col abs" style="left:641px"><h4>CUSTOMER SUPPORT</h4><a href="#">View Plans</a><a href="#">Contact Us</a><a href="#">Phone: +1(833)555-0142</a></div>
<div class="f-col social abs" style="left:925px"><h4 style="margin-left:9px">FOLLOW US</h4><a href="#"><i></i>Community Feed</a><a href="#"><i></i>Quick Posts</a><a href="#"><i></i>Video Channel</a><a href="#"><i></i>Photo Stream</a></div>
<div class="rule abs"></div>
<div class="copy abs">© Copyrights 2020 Keystone Signal &nbsp;|&nbsp; All Rights Reserved</div>

</body>
</html>
```